Verdant Systems Business Card

want the back of card to be blue- with the logo in the center
front of card- info plus logo (info being mailing address, email address, and website address )
4 different names with titles to have on cards
1) Calvin Borsted - Owner
2) Naomi Trelvik- Customer Relationship Specialist
3) Felix Andrade- Vice President of Sales
4) Owen Markby- Chief Technology Officer

Target Market(s)

tech company in the government/probation office industry

Industry/Entity Type

Government Office

Contact Information for Business Card

1) Calvin Borsted - Owner

Colors
0355a3
ffffff

Requirements
Must have
• back side should be blue, with the logo placed in the center
• front side needs to include both the logo, as well as company info (info should include website address, email address, and mailing address)

```html
<!DOCTYPE html>
<html lang="en">
<head>
<meta charset="utf-8">
<title>Verdant Systems Business Card</title>
<link rel="stylesheet" href="https://fonts.googleapis.com/css2?family=PT+Serif:wght@400;700&family=Roboto:wght@400&display=swap">
<style>
  :root {
    --navy: #263a6b;
    --navy-deep: #1b2b52;
    --grey: #8a8b94;
    --text-grey: #5f6068;
    --card: #ffffff;
    --backdrop: #e4e4e6;
  }
  * { margin: 0; padding: 0; box-sizing: border-box; }
  html, body { width: 1200px; height: 1200px; overflow: hidden; }
  body { background: var(--backdrop); position: relative; font-family: "Roboto", sans-serif; }

  .card {
    position: absolute;
    width: 712px;
    height: 417px;
    background: var(--card);
    border-radius: 22px;
    overflow: hidden;
  }
  .card--back { left: 238px; top: 120px; background: var(--navy); }
  .card--front { left: 230px; top: 644px; }

  .wordmark {
    position: absolute;
    text-align: center;
    font-family: "PT Serif", serif;
    font-weight: 700;
    color: var(--navy);
    line-height: 1.05;
    letter-spacing: 2px;
    text-transform: uppercase;
  }
  .wordmark .mark-dot {
    display: block;
    width: 54px; height: 54px;
    margin: 0 auto 14px;
    border-radius: 50%;
    background: var(--navy);
  }
  .card--back .wordmark { left: 0; right: 0; top: 88px; font-size: 58px; color: #fff; }
  .card--back .wordmark .mark-dot { background: #fff; }
  .card--front .wordmark { left: 30px; width: 340px; top: 102px; font-size: 44px; }
  .card--front .wordmark .mark-dot { width: 44px; height: 44px; margin-bottom: 12px; }

  .web-line {
    position: absolute;
    left: 0; right: 0; top: 374px;
    display: flex; justify-content: center; align-items: center; gap: 22px;
    font-size: 17px; color: #fff;
  }
  .web-line .rule { width: 46px; height: 3px; background: #fff; }

  .base-band { position: absolute; bottom: 0; height: 16px; }
  .base-band--navy { left: 0; width: 357px; background: var(--navy-deep); }
  .base-band--grey { left: 357px; right: 0; background: var(--grey); }

  .wave { position: absolute; left: 0; top: 0; width: 712px; height: 417px; }

  .person { position: absolute; right: 30px; top: 26px; text-align: right; color: #fff; }
  .person__name { font-family: "PT Serif", serif; font-size: 26px; letter-spacing: 1px; margin-bottom: 8px; }
  .person__title { font-size: 17px; line-height: 23px; }

  .address {
    position: absolute; left: 32px; top: 333px;
    font-size: 17px; line-height: 25px; color: var(--text-grey);
  }
  .contact {
    position: absolute; right: 30px; top: 306px;
    list-style: none; text-align: right;
    font-size: 17px; line-height: 26px; color: var(--text-grey);
  }
  .contact li { display: flex; justify-content: flex-end; align-items: center; gap: 10px; }
  .contact svg { width: 16px; height: 16px; fill: var(--navy); }
</style>
</head>
<body>

<section class="card card--back">
  <div class="wordmark"><span class="mark-dot"></span>Verdant<br>Systems</div>
  <div class="web-line"><span class="rule"></span>www.verdantsystems.com<span class="rule"></span></div>
  <div class="base-band base-band--navy"></div>
  <div class="base-band base-band--grey"></div>
</section>

<section class="card card--front">
  <svg class="wave" viewBox="0 0 712 417" aria-hidden="true">
    <path d="M0,0 H712 V150 C610,158 500,110 380,64 C250,20 110,18 0,36 Z" fill="var(--navy)"/>
    <path d="M0,44 C120,26 250,30 380,76 C500,118 610,168 712,162 V178 C610,186 500,140 380,100 C250,56 120,52 0,70 Z" fill="var(--grey)"/>
  </svg>

  <div class="person">
    <div class="person__name">NAOMI TRELVIK</div>
    <div class="person__title">Customer Relationship<br>Specialist</div>
  </div>

  <div class="wordmark"><span class="mark-dot"></span>Verdant<br>Systems</div>

  <p class="address">234 Anywhere St., Any City,<br>Any Town, US 123456</p>

  <ul class="contact">
    <li>111-111-1111
      <svg viewBox="0 0 24 24"><path d="M6.6 10.8a15 15 0 0 0 6.6 6.6l2.2-2.2c.3-.3.7-.4 1-.2 1.1.4 2.3.6 3.6.6.6 0 1 .4 1 1V20c0 .6-.4 1-1 1A17 17 0 0 1 3 4c0-.6.4-1 1-1h3.5c.6 0 1 .4 1 1 0 1.3.2 2.5.6 3.6.1.3 0 .7-.2 1z"/></svg>
    </li>
    <li>www.verdantsystems.com
      <svg viewBox="0 0 24 24"><path d="M12 2a10 10 0 1 0 0 20 10 10 0 0 0 0-20zm6.9 6h-3a15 15 0 0 0-1.3-3.9A8 8 0 0 1 18.9 8zM12 4c.8 1.2 1.5 2.5 1.9 4h-3.8c.4-1.5 1.1-2.8 1.9-4zM4.3 14a8 8 0 0 1 0-4h3.4a16 16 0 0 0 0 4zm.8 2h3a15 15 0 0 0 1.3 3.9A8 8 0 0 1 5.1 16zm3-8h-3a8 8 0 0 1 4.3-3.9C8.8 5.3 8.4 6.6 8.1 8zM12 20c-.8-1.2-1.5-2.5-1.9-4h3.8c-.4 1.5-1.1 2.8-1.9 4zm2.3-6H9.7a14 14 0 0 1 0-4h4.6a14 14 0 0 1 0 4zm.3 5.9c.6-1.2 1-2.5 1.3-3.9h3a8 8 0 0 1-4.3 3.9zm1.7-5.9a16 16 0 0 0 0-4h3.4a8 8 0 0 1 0 4z"/></svg>
    </li>
    <li>naomi.t@verdantsystems.com
      <svg viewBox="0 0 24 24"><path d="M3 5h18c.6 0 1 .4 1 1v12c0 .6-.4 1-1 1H3c-.6 0-1-.4-1-1V6c0-.6.4-1 1-1zm1 2.4V17h16V7.4l-8 5.3z M5 7l7 4.6L19 7z"/></svg>
    </li>
  </ul>
</section>

</body>
</html>
```